SOLVE Study flyer

I need help designing a flyer for a research study that will include brain imaging in adolescents. The info is in the attached document. The study is called the Sequoia Outlook Lantern Valley Echo (SOLVE) study. Ideally this would be returned as a document that I can edit in the future as we will have several new recruitment phases (different age groups, etc. I also would love to have a logo designed as part of this project, but I recognize that might be a separate design request.

```html
<!DOCTYPE html>
<html lang="en">
<head>
<meta charset="utf-8">
<title>SOLVE Study – Help Us to Understand Young Minds</title>
<link rel="stylesheet" href="https://fonts.googleapis.com/css2?family=Outfit:wght@600;700&family=Quicksand:wght@500;600;700&family=Gochi+Hand&display=swap">
<style>
  :root{
    --sky:#e3eef9;
    --navy:#0a2b5e;
    --ink:#0f2b5b;
    --royal:#0b5bb5;
    --gold:#fbbf3a;
    --cream:#fcf3e6;
    --white:#ffffff;
    --black:#1a1a1a;
  }
  *{box-sizing:border-box;margin:0;padding:0}
  html,body{width:927px;height:1200px;overflow:hidden;background:var(--white)}
  body{font-family:"Quicksand",sans-serif;color:var(--ink)}
  .flyer{position:relative;width:927px;height:1200px;overflow:hidden}

  .hero{position:absolute;left:0;top:0;width:927px;height:315px;background:var(--sky)}
  .hero__photo{position:absolute;left:631px;top:16px;width:296px;height:299px;
    background:radial-gradient(ellipse at 55% 45%, #f4d9a8 0%, #f6cf7a 45%, #e7eef6 78%);}
  .hero__kicker{position:absolute;left:45px;top:38px;font-family:"Outfit",sans-serif;font-weight:700;font-size:47.5px;letter-spacing:1px;color:var(--ink);white-space:nowrap}
  .hero__bar{position:absolute;left:0;top:120px;width:567px;height:86px;background:var(--gold)}
  .hero__title{position:absolute;left:66px;top:75px;font-family:"Gochi Hand",cursive;font-size:160px;line-height:1;color:var(--ink);white-space:nowrap;transform:scaleX(.47);transform-origin:left top}
  .hero__sub{position:absolute;left:41px;top:244px;font-size:27px;font-weight:600;color:var(--ink);white-space:nowrap}

  .intro{position:absolute;left:0;top:315px;width:927px;height:148px;background:var(--navy);padding:28px 40px 0 43px}
  .intro p{font-size:20px;font-weight:600;line-height:32px;letter-spacing:-.3px;color:var(--white)}
  .intro em{font-style:normal;font-weight:700;color:var(--gold)}

  .col{position:absolute;top:477px;height:485px;overflow:hidden}
  .col--what{left:0;width:475px;background:var(--white)}
  .col--who{left:475px;width:452px;background:var(--cream)}
  .col__head{position:absolute;left:0;top:0;width:100%;height:51px;display:flex;align-items:center;font-size:20.5px;font-weight:700}
  .col--what .col__head{background:var(--royal);color:var(--white);padding-left:19px}
  .col--who .col__head{background:var(--gold);color:var(--ink);justify-content:center}

  .icon{position:absolute;fill:none;stroke-linecap:round;stroke-linejoin:round}
  .col--what .icon{stroke:var(--ink);stroke-width:3}
  .col--who .icon{stroke:var(--black);stroke-width:2.6}
  .text{position:absolute;white-space:nowrap}
  .col--what .text{left:111px}
  .col--who .text{left:126px}
  .text__title{font-size:25px;font-weight:600;line-height:30px}
  .text__body{font-size:19.5px;font-weight:500;line-height:26px;color:var(--black)}
  .text__body--tight{line-height:25.5px}
  .crit{font-size:24px;font-weight:600;line-height:30px;color:var(--ink)}

  .footer{position:absolute;left:0;top:962px;width:927px;height:238px;background:var(--navy)}
  .cta__head{position:absolute;left:47px;top:44px;font-family:"Outfit",sans-serif;font-weight:700;font-size:44px;line-height:52px;color:var(--gold)}
  .cta__sub{position:absolute;left:47px;top:150px;font-size:27px;font-weight:600;color:var(--white)}
  .pay__rays{position:absolute;left:0;top:0}
  .pay__rays line{stroke:var(--gold);stroke-width:6;stroke-linecap:round}
  .pay__label{position:absolute;left:590px;top:38px;font-family:"Outfit",sans-serif;font-weight:600;font-size:27px;color:var(--white);letter-spacing:.5px}
  .pay__amount{position:absolute;left:563px;top:55px;font-family:"Gochi Hand",cursive;font-size:160px;line-height:1;color:var(--gold);white-space:nowrap;transform:scaleX(.42);transform-origin:left top}
  .contact{position:absolute;left:0;top:1164px;width:927px;text-align:center;font-size:20px;font-weight:500;color:var(--white)}
</style>
</head>
<body>
<main class="flyer">

  <header class="hero">
    <div class="hero__photo" role="img" aria-label="Photo of a smiling young girl wearing a headband and denim shirt, with a warm yellow glow behind her"></div>
    <h1 class="hero__kicker">HELP US TO UNDERSTAND</h1>
    <div class="hero__bar"></div>
    <div class="hero__title">YOUNG MINDS!</div>
    <p class="hero__sub">A study for parents of children ages 10-17</p>
  </header>

  <section class="intro">
    <p>Northbrook University researchers are seeking girls age 10-17 for a study about <em>brain activity</em> in <em>emotions</em> and <em>decision-making</em> and how they relate to <em>puberty</em>, <em>anxiety</em> and <em>depression</em>.</p>
  </section>

  <section class="col col--what">
    <div class="col__head">A study for parents of children ages 10-17</div>

    <svg class="icon" style="left:19px;top:90px" width="74" height="54" viewBox="0 0 74 54">
      <rect x="5" y="3" width="64" height="40" rx="3"/>
      <path d="M2 43h70v6a3 3 0 0 1-3 3H5a3 3 0 0 1-3-3z"/>
      <circle cx="37" cy="18" r="7"/>
      <path d="M24 38c2-7 7-10 13-10s11 3 13 10"/>
    </svg>
    <div class="text" style="top:82px">
      <div class="text__title">One hour interview</div>
      <div class="text__body">(online or in-person)<br>where your child will discuss their<br>thoughts</div>
    </div>

    <svg class="icon" style="left:21px;top:211px" width="72" height="70" viewBox="0 0 72 70">
      <path d="M24 3a21 21 0 0 0-19 30l-3 10 11-3A21 21 0 1 0 24 3z"/>
      <path d="M20 16a5 5 0 1 1 6 5v3"/><circle cx="26" cy="30" r="1"/>
      <path d="M47 26a19 19 0 0 1 18 27l3 12-11-3a19 19 0 0 1-27-12"/>
      <path d="M40 42h16M40 48h16"/>
    </svg>
    <div class="text" style="top:222px">
      <div class="text__title">Online questionnaires</div>
      <div class="text__body">for both parent &amp; child</div>
    </div>

    <svg class="icon" style="left:20px;top:337px" width="72" height="72" viewBox="0 0 72 72">
      <path d="M6 70V36a30 30 0 0 1 60 0v34z"/>
      <path d="M16 36a20 20 0 0 1 40 0"/>
      <path d="M24 22a14 14 0 0 1 24 0"/>
      <rect x="27" y="34" width="18" height="14" rx="6"/>
      <path d="M22 48h28M6 70l12-14h36l12 14M36 56v14"/>
    </svg>
    <div class="text" style="top:323px">
      <div class="text__title">One 2-hour visit</div>
      <div class="text__body text__body--tight">includes an MRI scan, answering<br>questions about their puberty<br>stage, and a small hair sample to<br>study puberty hormones</div>
    </div>
  </section>

  <section class="col col--who">
    <div class="col__head">Is your child Eligible?</div>

    <svg class="icon" style="left:45px;top:98px" width="60" height="46" viewBox="0 0 60 46">
      <circle cx="30" cy="9" r="7"/><circle cx="10" cy="16" r="5"/><circle cx="50" cy="16" r="5"/>
      <path d="M16 44c0-10 6-17 14-17s14 7 14 17"/>
      <path d="M2 44c0-8 3-13 9-14M58 44c0-8-3-13-9-14"/>
    </svg>
    <div class="text crit" style="top:105px">Are age 10-17</div>

    <svg class="icon" style="left:48px;top:197px" width="54" height="58" viewBox="0 0 54 58">
      <path d="M16 56V46c-8-4-12-12-11-20C6 12 16 3 29 3c13 0 22 9 22 22 0 8-4 13-9 17v14"/>
      <path d="M5 30l-3 6h5"/>
      <path d="M31 12l-8 14h8l-5 12 10-16h-8z"/>
    </svg>
    <div class="text crit" style="top:193px">Trend to worry or<br>overthink negative<br>thoughts</div>

    <svg class="icon" style="left:48px;top:328px" width="54" height="52" viewBox="0 0 54 52">
      <path d="M12 6H3v44h26M38 6h5v16"/>
      <path d="M17 3v6M23 3v6M29 3v6"/>
      <path d="M11 20h22M11 28h22M11 36h12"/>
      <path d="M45 26l6 6-16 16-8 2 2-8z"/>
    </svg>
    <div class="text crit" style="top:324px">Have not been<br>diagnosed with<br>psychosis, learning<br>problems, or autism</div>
  </section>

  <footer class="footer">
    <div class="cta__head">Interested In<br>Participating?</div>
    <div class="cta__sub">Please Contact Us</div>

    <svg class="pay__rays" width="927" height="238" viewBox="0 0 927 238">
      <line x1="463" y1="48" x2="530" y2="83"/>
      <line x1="451" y1="113" x2="526" y2="113"/>
      <line x1="463" y1="178" x2="530" y2="143"/>
      <line x1="927" y1="48" x2="866" y2="83"/>
      <line x1="927" y1="113" x2="870" y2="113"/>
      <line x1="927" y1="178" x2="866" y2="143"/>
    </svg>
    <div class="pay__label">COMPENSATION</div>
    <div class="pay__amount">UP TO $140</div>
  </footer>

  <div class="contact">solvestudy@northbrookhealth.edu</div>
</main>
</body>
</html>
```